SkyvornQ Business Cards and Stationary Design

Need a design for our business cards and stationary. I want to carry on the theme of the logo. I want the business cards to have a design on the back. I would like the business cards and the stationary to carry the same theme, design scheme, and branding

Target Market(s)

Airlines and Maintenance Facilities

Industry/Entity Type

Aviation

Contact Information for Business Card

Name
Position Title
Address: 4827 Trellis Hollow Road, Fort Pierce, Florida, 34951
Office Number
Mobile Number
Email
Website

Font styles to use
Serif
Sans Serif

Colors

Designer to choose colors to be used in the design.

```html
<!DOCTYPE html>
<html lang="en">
<head>
<meta charset="utf-8">
<title>SkyvornQ Business Card</title>
<link rel="stylesheet" href="https://fonts.googleapis.com/css2?family=Open+Sans:wght@400;600;700&display=swap">
<style>
  :root {
    --navy: #0c2a56;
    --navy-deep: #08204a;
    --sky: #1b8fd6;
    --sky-dark: #0f5fa8;
    --white: #ffffff;
    --bg: #e9ecf1;
    --font: "Open Sans", Arial, sans-serif;
  }
  * { box-sizing: border-box; margin: 0; padding: 0; }
  html, body { width: 1200px; height: 872px; overflow: hidden; }
  body {
    background: var(--bg);
    font-family: var(--font);
    position: relative;
  }
  .card {
    position: absolute;
    left: 290px;
    width: 620px;
    height: 354px;
    overflow: hidden;
    box-shadow: 0 8px 24px rgba(8, 32, 74, 0.18);
  }
  .card--back { top: 52px; background: var(--navy); }
  .card--front { top: 466px; background: var(--white); }

  /* back */
  .back-brand {
    position: absolute;
    left: 0; right: 0; top: 118px;
    display: flex; align-items: center; justify-content: center; gap: 18px;
  }
  .brand-dot {
    width: 54px; height: 54px; border-radius: 50%;
    border: 5px solid var(--white);
  }
  .brand-name {
    font-weight: 700; letter-spacing: 6px; font-size: 44px; color: var(--white);
  }
  .back-url {
    position: absolute; left: 0; right: 0; top: 206px;
    text-align: center; color: var(--white);
    font-size: 16px; letter-spacing: 3px;
  }

  /* front */
  .front-shapes { position: absolute; inset: 0; }
  .front-brand {
    position: absolute; left: 34px; top: 128px; width: 300px;
    display: flex; flex-direction: column; align-items: center; gap: 14px;
  }
  .front-brand .brand-dot { border-color: var(--sky-dark); width: 70px; height: 70px; }
  .front-brand .brand-name { color: var(--navy); font-size: 38px; letter-spacing: 5px; }

  .person {
    position: absolute; right: 30px; top: 72px; text-align: right; color: var(--white);
  }
  .person-name { font-weight: 700; font-size: 21px; letter-spacing: 0.5px; }
  .person-title { font-size: 17px; letter-spacing: 0.5px; }

  .contacts {
    position: absolute; right: 30px; top: 160px;
    list-style: none; color: var(--white); font-size: 14px;
  }
  .contacts li {
    display: flex; align-items: center; justify-content: flex-end; gap: 6px;
    height: 21px;
  }
  .contacts svg { width: 13px; height: 13px; flex: none; }
  .contacts .address { margin-top: 14px; align-items: flex-start; height: auto; }
  .address-text { text-align: right; line-height: 1.4; }
</style>
</head>
<body>

<section class="card card--back" aria-label="Business card back">
  <div class="back-brand">
    <span class="brand-dot"></span>
    <span class="brand-name">SKYVORNQ</span>
  </div>
  <p class="back-url">www.skyvornq.com</p>
</section>

<section class="card card--front" aria-label="Business card front">
  <svg class="front-shapes" width="620" height="354" viewBox="0 0 620 354" aria-hidden="true">
    <defs>
      <linearGradient id="ribbon" x1="0" y1="0" x2="1" y2="0">
        <stop offset="0" stop-color="#23a4e6"/>
        <stop offset="1" stop-color="#0e4f9a"/>
      </linearGradient>
    </defs>
    <polygon points="360,0 620,0 620,354 330,354" fill="var(--navy)"/>
    <polygon points="290,132 350,132 350,172" fill="var(--sky-dark)"/>
    <polygon points="272,68 620,68 620,126 290,132" fill="url(#ribbon)"/>
  </svg>

  <div class="front-brand">
    <span class="brand-dot"></span>
    <span class="brand-name">SKYVORNQ</span>
  </div>

  <div class="person">
    <p class="person-name">MARCUS DELANY</p>
    <p class="person-title">PRESIDENT</p>
  </div>

  <ul class="contacts">
    <li>
      <svg viewBox="0 0 16 16"><circle cx="8" cy="8" r="7" fill="none" stroke="#fff" stroke-width="1.3"/><path d="M5.5 4.5l1.4 1.6-.8 1c.6 1.2 1.4 2 2.6 2.6l1-.8 1.6 1.4-.9 1.2C8 11.3 4.9 8.4 4.4 5.4z" fill="#fff"/></svg>
      <span>012-345-6789</span>
    </li>
    <li>
      <svg viewBox="0 0 16 16"><circle cx="8" cy="8" r="7" fill="none" stroke="#fff" stroke-width="1.3"/><rect x="5.8" y="4" width="4.4" height="8" rx="0.8" fill="none" stroke="#fff" stroke-width="1.2"/></svg>
      <span>012-345-6789</span>
    </li>
    <li>
      <svg viewBox="0 0 16 16"><circle cx="8" cy="8" r="7" fill="none" stroke="#fff" stroke-width="1.3"/><rect x="4.3" y="5.3" width="7.4" height="5.4" fill="none" stroke="#fff" stroke-width="1.1"/><path d="M4.3 5.5L8 8.4l3.7-2.9" fill="none" stroke="#fff" stroke-width="1.1"/></svg>
      <span>info@skyvornq.com</span>
    </li>
    <li>
      <svg viewBox="0 0 16 16"><circle cx="8" cy="8" r="7" fill="none" stroke="#fff" stroke-width="1.3"/><ellipse cx="8" cy="8" rx="3" ry="7" fill="none" stroke="#fff" stroke-width="1"/><path d="M1 8h14M2.5 4.5h11M2.5 11.5h11" stroke="#fff" stroke-width="1"/></svg>
      <span>www.skyvornq.com</span>
    </li>
    <li class="address">
      <svg viewBox="0 0 16 16"><circle cx="8" cy="8" r="7" fill="none" stroke="#fff" stroke-width="1.3"/><path d="M8 12.5S5 9 5 7a3 3 0 016 0c0 2-3 5.5-3 5.5z" fill="none" stroke="#fff" stroke-width="1.1"/><circle cx="8" cy="7" r="1" fill="#fff"/></svg>
      <span class="address-text">Street Name, City Name<br>Zipcode-012345</span>
    </li>
  </ul>
</section>

</body>
</html>
```